Satchel & Sundial needs new business card design

I need a new business card design. I'm looking for out-of-the-box design which represents the freedom of being a location independent entrepreneur.
I offer coaching, retreats and trips.
I would like to see designs with and without the photo.
Colors I use are black (#000000), green (#25A796) and brown (#D7C38C)
Website satchelandsundial.example

Target Market(s)

location independent entrepreneurs, digital nomads, people looking to swap the 9 to 5 for a lifestyle business

Industry/Entity Type

Business

Contact Information for Business Card

Dorota Falkner
Your Lifestyle Business Coach, Retreat & Trip Leader
http://satchelandsundial.example
hello@satchelandsundial.example
Live a life you don't need a holiday from

Font styles to use
Serif
Sans Serif

Requirements
Must have
• One side should contain only the logo. I would also consider having the "Live a life you don't need a holiday from" on that side too (depending on how it looks)
• Please show both sides on the designs.

```html
<!DOCTYPE html>
<html lang="en">
<head>
<meta charset="utf-8">
<title>Satchel &amp; Sundial – Business Card</title>
<link rel="stylesheet" href="https://fonts.googleapis.com/css2?family=Oswald:wght@300;400;500&display=swap">
<style>
  :root {
    --backdrop: #e4e4e4;
    --card: #f8f8f8;
    --ink: #111111;
    --green: #1f9c8b;
    --brown: #d7c38c;
    --photo-top: #8f9a78;
    --photo-bottom: #5f6f52;
  }
  * { box-sizing: border-box; margin: 0; padding: 0; }
  html, body {
    width: 1200px;
    height: 576px;
    overflow: hidden;
    background: var(--backdrop);
    font-family: "Oswald", "Arial Narrow", sans-serif;
    color: var(--ink);
  }
  .canvas { position: relative; width: 1200px; height: 576px; }
  .card {
    position: absolute;
    top: 138px;
    width: 484px;
    height: 294px;
    background: var(--card);
    border-radius: 6px;
    overflow: hidden;
  }
  .card--front { left: 81px; }
  .card--back { left: 602px; }

  /* Front */
  .wordmark {
    position: absolute;
    top: 98px;
    left: 0;
    width: 100%;
    text-align: center;
    font-size: 44px;
    font-weight: 400;
    letter-spacing: 1px;
    text-transform: uppercase;
    color: var(--ink);
  }
  .front-web {
    position: absolute;
    top: 250px;
    left: 0;
    width: 100%;
    display: flex;
    justify-content: center;
    align-items: center;
    gap: 14px;
    font-size: 12px;
    font-weight: 400;
  }
  .front-web .rule {
    width: 46px;
    height: 2px;
    background: var(--brown);
    border-radius: 2px;
  }
  .front-web .accent { color: var(--green); }

  /* Back */
  .photo { position: absolute; left: 0; top: 0; }
  .details {
    position: absolute;
    right: 27px;
    top: 32px;
    text-align: right;
  }
  .details__name {
    font-size: 22px;
    font-weight: 500;
    color: var(--green);
    text-transform: uppercase;
    line-height: 1.1;
  }
  .details__role {
    font-size: 11.5px;
    font-weight: 400;
    line-height: 1.3;
    margin-top: 4px;
  }
  .contacts {
    position: absolute;
    right: 27px;
    top: 154px;
    list-style: none;
    text-align: right;
  }
  .contacts li {
    display: flex;
    justify-content: flex-end;
    align-items: center;
    gap: 6px;
    font-size: 12.5px;
    font-weight: 400;
    height: 21px;
  }
  .contacts svg { width: 11px; height: 11px; }
  .contacts .social-dot {
    width: 10px; height: 10px;
    background: var(--green);
    border-radius: 2px;
  }
  .tagline {
    position: absolute;
    right: 27px;
    top: 236px;
    font-size: 14px;
    font-weight: 400;
    color: var(--green);
  }
</style>
</head>
<body>
<main class="canvas">
  <section class="card card--front" aria-label="Card front">
    <h1 class="wordmark">Satchel &amp; Sundial</h1>
    <p class="front-web">
      <span class="rule"></span>
      <span>www.<span class="accent">satchelandsundial</span>.example</span>
      <span class="rule"></span>
    </p>
  </section>

  <section class="card card--back" aria-label="Card back">
    <svg class="photo" width="484" height="294" viewBox="0 0 484 294">
      <defs>
        <linearGradient id="photoTone" x1="0" y1="0" x2="0" y2="1">
          <stop offset="0" stop-color="var(--photo-top)"/>
          <stop offset="1" stop-color="var(--photo-bottom)"/>
        </linearGradient>
      </defs>
      <path role="img" aria-label="Photo of the coach seated outdoors among trees, holding a small chalkboard sign"
            d="M0 0 H166 Q262 140 186 294 H0 Z" fill="url(#photoTone)"/>
      <path d="M166 0 H182 Q262 150 190 294 H186 Q250 145 166 0 Z" fill="var(--green)"/>
    </svg>

    <div class="details">
      <h2 class="details__name">Dorota Falkner</h2>
      <p class="details__role">Your Lifestyle Business Coach<br>Retreat &amp; Trip Leader</p>
    </div>

    <ul class="contacts">
      <li>hello@satchelandsundial.example
        <svg viewBox="0 0 12 12" aria-hidden="true"><rect x="0.5" y="2" width="11" height="8" fill="var(--green)"/><path d="M0.5 2 L6 6.5 L11.5 2" stroke="#fff" stroke-width="1" fill="none"/></svg>
      </li>
      <li>www.satchelandsundial.example
        <svg viewBox="0 0 12 12" aria-hidden="true"><circle cx="6" cy="6" r="5" fill="none" stroke="var(--green)" stroke-width="1.2"/><ellipse cx="6" cy="6" rx="2.2" ry="5" fill="none" stroke="var(--green)" stroke-width="1"/><line x1="1" y1="6" x2="11" y2="6" stroke="var(--green)" stroke-width="1"/></svg>
      </li>
      <li>/satchelandsundial <span class="social-dot"></span></li>
    </ul>

    <p class="tagline">Live a life you don't need a holiday from</p>
  </section>
</main>
</body>
</html>
```